Brand new letterhead, business card, email signature etc.

We are a financial company in London, UK. Our website is www.marlowvane.com. We're wanting a complete remodel of the company colours, letter head, business cards, email signatures, etc. Looking to keep the same font for the company name. I have upload a colour palette that we want to work with. We're looking for company letterhead for outgoing letters/ correspondence, letterhead for internal documentation, email signatures, e-letters. etc. Ultimately we will redesign the entire website also. It is important that our clients get a strong, secure, warm, trustworthy, solid feeling and first impression.
Updates

Designs look the same

Target Market(s)

Institutional investors, (ultra) high net worth individuals

Industry/Entity Type

Finance, Invesments banking.

Font styles to use
Other font styles liked:
• Current font is "Champagne & Limousines"

Requirements
Must have
• Must use the colours provided on the PDF uploaded to the portal. The purple = main colour. The red = accent colour.
Nice to have
• Nice to use same font as now for the company name "Corvane". Font is "Champagne & Limousines". Nice to have some reference to the old logo flower, but only subtle.
Should not have
• Do not use the colour red from our website. Use the colours provided on the colour palette PDF that I uploaded in the portal.

```html
<!DOCTYPE html>
<html lang="en">
<head>
<meta charset="utf-8">
<title>Corvane Business Card</title>
<link rel="stylesheet" href="https://fonts.googleapis.com/css2?family=Josefin+Sans:wght@300;400;600&display=swap">
<style>
  :root {
    --backdrop: #2e2d2d;
    --card: #ffffff;
    --card-shade: #ececec;
    --plum: #2a0a1a;
    --accent: #d9361e;
    --ink: #2b2b2b;
    --band-text: #e9e2e5;
  }
  * { box-sizing: border-box; margin: 0; padding: 0; }
  html, body {
    width: 1200px;
    height: 900px;
    overflow: hidden;
    background: var(--backdrop);
    font-family: "Josefin Sans", "Century Gothic", sans-serif;
  }
  .stage {
    width: 1200px;
    height: 900px;
    display: flex;
    flex-direction: column;
    align-items: center;
    justify-content: center;
    gap: 44px;
  }
  .card {
    position: relative;
    width: 620px;
    height: 354px;
    background: linear-gradient(160deg, var(--card) 55%, var(--card-shade));
    overflow: hidden;
    box-shadow: 0 10px 28px rgba(0,0,0,0.45);
  }
  .wordmark {
    font-weight: 300;
    color: var(--ink);
    letter-spacing: 0.28em;
    text-transform: uppercase;
  }
  .card-front .wordmark {
    position: absolute;
    top: 34px;
    right: 30px;
    font-size: 30px;
  }
  .holder {
    position: absolute;
    left: 36px;
    top: 176px;
  }
  .holder-name {
    font-size: 21px;
    font-weight: 400;
    letter-spacing: 0.16em;
    color: var(--ink);
    text-transform: uppercase;
  }
  .holder-title {
    margin-top: 4px;
    font-size: 14px;
    color: var(--accent);
  }
  .info-band {
    position: absolute;
    left: 0;
    right: 0;
    bottom: 0;
    height: 124px;
    background: var(--plum);
    border-top: 7px solid var(--accent);
    display: flex;
    justify-content: space-between;
    padding: 20px 30px 0 58px;
    color: var(--band-text);
  }
  .contact-list { list-style: none; }
  .contact-list li {
    display: flex;
    align-items: center;
    gap: 12px;
    font-size: 15px;
    line-height: 24px;
    letter-spacing: 0.03em;
  }
  .contact-list .web { font-weight: 600; }
  .contact-list svg { width: 13px; height: 13px; flex: none; }
  .address {
    font-style: normal;
    text-align: right;
    font-size: 15px;
    line-height: 19px;
    letter-spacing: 0.02em;
  }
  .card-back {
    display: flex;
    align-items: center;
    justify-content: center;
  }
  .card-back .wordmark { font-size: 36px; padding-left: 0.28em; }
</style>
</head>
<body>
<main class="stage">
  <section class="card card-front" aria-label="Business card front">
    <div class="wordmark">Corvane</div>
    <div class="holder">
      <p class="holder-name">Edward Lanning</p>
      <p class="holder-title">chairman</p>
    </div>
    <div class="info-band">
      <ul class="contact-list">
        <li>
          <svg viewBox="0 0 16 16" aria-hidden="true"><path fill="#d9361e" d="M3 1.5h3l1.2 3.3-1.8 1.3a9 9 0 0 0 4.5 4.5l1.3-1.8 3.3 1.2v3c0 .8-.7 1.5-1.5 1.5A13 13 0 0 1 1.5 3c0-.8.7-1.5 1.5-1.5z"/></svg>
          +4470 5550 1286
        </li>
        <li>
          <svg viewBox="0 0 16 16" aria-hidden="true"><rect x="1" y="3" width="14" height="10" rx="1" fill="#d9361e"/><path d="M1.5 3.8 8 9l6.5-5.2" fill="none" stroke="#2a0a1a" stroke-width="1.4"/></svg>
          e@marlowvane.com
        </li>
        <li class="web">
          <svg viewBox="0 0 16 16" aria-hidden="true"><circle cx="8" cy="8" r="7" fill="#d9361e"/><g fill="none" stroke="#2a0a1a" stroke-width="1"><ellipse cx="8" cy="8" rx="3" ry="7"/><path d="M1 8h14M2.5 4.5h11M2.5 11.5h11"/></g></svg>
          www.marlowvane.com
        </li>
      </ul>
      <address class="address">
        14 Ashby Court<br>
        EC3M 2PL, London<br>
        United Kingdom
      </address>
    </div>
  </section>

  <section class="card card-back" aria-label="Business card back">
    <div class="wordmark">Corvane</div>
  </section>
</main>
</body>
</html>
```